Brookvale Estates LLC stationary for a real estate property management company.

Create stationary (letterhead, envelopes, business cards) using Brookvale Estates LLC logo as primary creative element. Stationary design needs to be horizontal, leaving as much space as possible for correspondence copy. See attached Creative Brief and past stationary files for details.

Target Market(s)

Prospective apartment residents and current residents, vendors, and government agencies.

Industry/Entity Type

Property Management

Contact Information for Business Card

Business card employee title: Property Manager. Should include address, phone, fax, email, website, slogan, and Brookvale Estates logo.

Font styles to use
Sans Serif

Colors
0592cd
000000

Requirements
Must have
• Tone should be conservative, institutional, business (i.e. banking, finance, real estate). Must include: address, phone, fax, website, and slogan (see attached Creative Brief). Should be a horizontal design, leaving as much room as possible for letter correspondence copy.
Nice to have
• Please use an Arial or Helvetica style font.
Should not have
• Letterhead layout should leave as much room as possible for copy.

```html
<!DOCTYPE html>
<html lang="en">
<head>
<meta charset="utf-8">
<title>Brookvale Estates LLC – Stationery</title>
<link rel="stylesheet" href="https://fonts.googleapis.com/css2?family=Arimo:wght@400;700&family=Source+Sans+3:wght@400&display=swap">
<style>
  :root {
    --brand-blue: #0e63a3;
    --charcoal: #444547;
    --ink: #2b2b2b;
    --body-ink: #4a4a4a;
    --paper: #f7f7f7;
    --paper-white: #ffffff;
    --envelope-back: #ececec;
    --stage: #d9d6d2;
  }
  * { margin: 0; padding: 0; box-sizing: border-box; }
  html, body { width: 1200px; height: 754px; overflow: hidden; }
  body { background: var(--stage); position: relative; font-family: "Arimo", Arial, sans-serif; color: var(--ink); }

  .sheet { position: absolute; }

  /* Brand name lockup */
  .brand-name {
    font-family: "Arimo", Arial, sans-serif;
    font-weight: 700;
    color: var(--brand-blue);
    line-height: 1;
    text-transform: uppercase;
  }
  .brand-name span { display: block; }
  .brand-name .line-sub { letter-spacing: 0.16em; }

  /* Letterhead */
  .letterhead { left: 36px; top: 32px; width: 488px; height: 688px; background: var(--paper); }
  .letterhead .brand-band { position: absolute; left: 0; top: 52px; width: 70px; height: 46px; background: var(--brand-blue); }
  .letterhead .brand-name { position: absolute; left: 86px; top: 62px; font-size: 19px; }
  .letterhead .brand-name .line-sub { font-size: 9px; margin-top: 3px; letter-spacing: 0.2em; }
  .letterhead .contact { position: absolute; right: 46px; top: 45px; text-align: right; font-size: 8px; line-height: 10px; color: var(--ink); }
  .letterhead .contact li { list-style: none; display: flex; justify-content: flex-end; align-items: center; gap: 4px; }
  .letterhead .contact .addr { display: block; }
  .letterhead .contact svg { width: 7px; height: 7px; fill: var(--brand-blue); }
  .letter-body { position: absolute; left: 49px; top: 194px; width: 394px; font-family: "Source Sans 3", sans-serif; color: var(--body-ink); }
  .letter-body .greeting { font-size: 14px; margin-bottom: 26px; color: #555; }
  .letter-body p { font-size: 7.4px; line-height: 11.8px; margin-bottom: 11px; text-align: justify; }
  .letter-body .closing { margin-top: 20px; }
  .signature-area { width: 64px; height: 26px; margin-top: 6px; background: linear-gradient(90deg, #d8d8d8, #e8e8e8); border-radius: 3px; }

  /* Business card front */
  .card-front { left: 578px; top: 74px; width: 266px; height: 152px; background: var(--paper); }
  .card-front .brand-band { position: absolute; left: 0; top: 0; width: 36px; height: 152px; background: var(--brand-blue); }
  .card-front .details { position: absolute; right: 12px; top: 18px; text-align: right; }
  .card-front .brand-name { font-size: 17px; }
  .card-front .brand-name .line-sub { font-size: 8px; margin-top: 2px; }
  .card-front .person { margin-top: 7px; font-size: 9.5px; font-weight: 700; color: var(--brand-blue); line-height: 1; }
  .card-front .role { font-size: 6.6px; color: var(--ink); margin-top: 1px; }
  .card-front .small { font-size: 5.8px; line-height: 7.8px; color: var(--ink); }
  .card-front .addr { margin-top: 5px; }
  .card-front .lines { margin-top: 4px; }
  .card-front .slogan { margin-top: 4px; font-size: 6.4px; font-weight: 700; color: var(--brand-blue); }

  /* Business card back */
  .card-back { left: 876px; top: 144px; width: 268px; height: 152px; background: var(--charcoal); display: flex; align-items: center; justify-content: center; }
  .card-back .brand-name { font-size: 23px; }
  .card-back .brand-name .line-sub { font-size: 9.5px; margin-top: 3px; letter-spacing: 0.2em; }

  /* Envelope back */
  .envelope-back { left: 615px; top: 350px; width: 548px; height: 248px; background: var(--envelope-back); }
  .envelope-back .flap { position: absolute; left: 0; top: 0; width: 548px; height: 92px; }
  .envelope-back .web { position: absolute; left: 0; right: 0; top: 62px; text-align: center; font-size: 8px; color: #fff; }

  /* Envelope front */
  .envelope-front { left: 547px; top: 470px; width: 549px; height: 250px; background: var(--paper-white); box-shadow: 0 0 0 1px #e0e0e0; }
  .envelope-front .brand-band { position: absolute; left: 0; top: 24px; width: 38px; height: 40px; background: var(--brand-blue); }
  .envelope-front .brand-name { position: absolute; left: 64px; top: 36px; font-size: 17px; }
  .envelope-front .brand-name .line-sub { font-size: 7.8px; margin-top: 2px; }
  .envelope-front .return-addr { position: absolute; left: 38px; top: 72px; font-size: 8px; line-height: 9.6px; color: var(--ink); }
</style>
</head>
<body>

  <section class="sheet letterhead">
    <div class="brand-band"></div>
    <div class="brand-name"><span class="line-main">Brookvale</span><span class="line-sub">Estates LLC</span></div>
    <ul class="contact">
      <li class="addr">2750 Linden Ridge Road #B210</li>
      <li class="addr">Fairhaven, CA 90000</li>
      <li>555-014-2278 <svg viewBox="0 0 10 10"><path d="M2 0h2l1 3-1.5 1a6 6 0 0 0 2.5 2.5L7 5l3 1v2c0 1-1 2-2 2A8 8 0 0 1 0 2c0-1 1-2 2-2z"/></svg></li>
      <li>555-014-3390 <svg viewBox="0 0 10 10"><rect x="2.5" y="0" width="5" height="3"/><rect x="0" y="3.5" width="10" height="4" rx="1"/><rect x="2.5" y="7" width="5" height="3"/></svg></li>
      <li>daniel@brookvaleestates.us <svg viewBox="0 0 10 10"><rect x="0" y="2" width="10" height="7" rx="1"/></svg></li>
      <li>www.brookvaleestates.us <svg viewBox="0 0 10 10"><circle cx="5" cy="5" r="5"/></svg></li>
    </ul>

    <article class="letter-body">
      <p class="greeting">Dear Mr. Carter,</p>
      <p>Lorem ipsum dolor sit amet, consectetur adipiscing elit. Donec orci purus, luctus vitae dignissim eu, iaculis sed purus. Vivamus faucibus, ipsum nec aliquet viverra, leo mauris condimentum ligula, sit amet sagittis enim ligula quis arcu. Nam egestas tortor id nisi porttitor mattis. In tortor ante, ultricies in suscipit a, tempus non massa. Vivamus et auctor mi. Fusce vel massa nulla. Phasellus nec eros mauris, et scelerisque orci.</p>
      <p>Donec malesuada orci vitae nulla accumsan porta a id massa. Quisque accumsan iaculis magna sit amet fringilla. Maecenas consequat, magna eget tincidunt semper, odio nibh rutrum mi, id feugiat ante nisi eu risus. Vestibulum nunc orci, rhoncus a placerat in, ultricies in mi. Cras mattis varius eros, vel fringilla nisi suscipit eget. Quisque scelerisque sagittis nulla at porttitor.</p>
      <p>Sed id augue vitae urna euismod commodo aliquet a quam. Pellentesque arcu velit, cursus et malesuada ut, consequat et diam. Nullam erat sem, rhoncus id ullamcorper vitae, rhoncus et arcu. In ultricies ultricies nulla, ut rutrum nisi iaculis at. Donec eu magna a metus ornare faucibus. Fusce aliquet faucibus ultricies. Morbi semper, est id tincidunt gravida, sem arcu adipiscing lacus, ac bibendum nulla leo eu purus. Quisque nec diam sed risus consectetur a accumsan quis quis nibh. Vestibulum id purus lorem.</p>
      <p>It is a long established fact that a reader will be distracted by the readable content of a page when looking at its layout. The point of using Lorem Ipsum is that it has a more-or-less normal distribution of letters, as opposed to using 'Content here, content here', making it look like readable English. Many desktop publishing packages</p>
      <p class="closing">Sincerely,</p>
      <div class="signature-area" role="img" aria-label="Handwritten signature"></div>
    </article>
  </section>

  <section class="sheet card-front">
    <div class="brand-band"></div>
    <div class="details">
      <div class="brand-name"><span class="line-main">Brookvale</span><span class="line-sub">Estates LLC</span></div>
      <p class="person">DANIEL HARGROVE</p>
      <p class="role">Property Manager</p>
      <p class="small addr">2750 Linden Ridge Road #B210<br>Fairhaven, CA 90000</p>
      <p class="small lines">Phone: 555-014-2278<br>Fax: 555-014-3390<br>daniel@brookvaleestates.us<br>www.brookvaleestates.us</p>
      <p class="slogan">Multifamily Property Management</p>
    </div>
  </section>

  <section class="sheet card-back">
    <div class="brand-name"><span class="line-main">Brookvale</span><span class="line-sub">Estates LLC</span></div>
  </section>

  <section class="sheet envelope-back">
    <svg class="flap" viewBox="0 0 548 92" preserveAspectRatio="none" aria-hidden="true">
      <path d="M0 0H548C548 0 545 20 536 60C530 84 520 92 500 92H48C28 92 18 84 12 60C3 20 0 0 0 0Z" fill="var(--charcoal)"/>
    </svg>
    <p class="web">www.brookvaleestates.us</p>
  </section>

  <section class="sheet envelope-front">
    <div class="brand-band"></div>
    <div class="brand-name"><span class="line-main">Brookvale</span><span class="line-sub">Estates LLC</span></div>
    <p class="return-addr">2750 Linden Ridge Road #B210<br>Fairhaven, CA 90000</p>
  </section>

</body>
</html>
```